a business advisory consulting website

I need a website 3-5 pages to sell my professional services in IT and Project management Consulting. My company name is Crestline Advisory Consulting. I want it to be device friendly and easy to navigate for the busy executive however intriguing enough.
I have attached some info I drafted on About the company and personal Bio. Also there is a website that I really like that I have attached the initial site pdf and websites that I like are here: https://tollmeradvisors.example, https://quarvelanalytics.example, https://www.dorvikstudylearning.example as examples. Thanks
Updates

Hi Designers, I have uploaded the logo in 3D .png format, to assist in the web design.

Target Market(s)

B2B, governments, IT companies, Project Management companies and Consulting firms, small medium enterprises to large corporate enterprises.

Industry/Entity Type

It Professional

Coding

Coded - Design and coding required

Number of Pages Required

5+ page

Font styles to use
Sans Serif

Requirements
Must have
• Home, About company, the team, what we do and contact us
Nice to have
• Blog
Should not have
• pop ups, flash

```html
<!DOCTYPE html>
<html lang="en">
<head>
<meta charset="utf-8">
<title>Crestline Advisory</title>
<link href="https://fonts.googleapis.com/css2?family=Bitter:wght@400;600;700&family=Open+Sans:wght@400;600;700&family=Montserrat:wght@700&display=swap" rel="stylesheet">
<style>
:root{
  --navy:#1d2440;
  --ink:#0e1322;
  --red:#d3161c;
  --grey-band:#f6f3f4;
  --text:#2b2d33;
  --white:#ffffff;
  --footer:#111729;
  --footer-line:#3a4156;
}
*{margin:0;padding:0;box-sizing:border-box}
html,body{width:1200px;height:3541px;overflow:hidden;background:var(--white)}
body{position:relative;font-family:"Open Sans",sans-serif;color:var(--text)}
.abs{position:absolute}

/* hero */
.hero{left:0;top:0;width:1200px;height:680px;
  background:linear-gradient(180deg,#e8eef4 0%,#9fb2c6 30%,#4d6480 55%,#2a3950 75%,#3c2f2f 100%)}
.hero-light{left:0;top:0;width:1200px;height:680px;
  background:radial-gradient(ellipse at 50% 30%,rgba(255,255,255,.7) 0%,rgba(255,255,255,0) 45%),
  linear-gradient(90deg,rgba(20,30,50,.55) 0%,rgba(20,30,50,0) 30%,rgba(20,30,50,0) 70%,rgba(20,30,50,.5) 100%)}
.hero-shape{left:0;top:0}
.brand{left:344px;top:30px;width:200px;height:62px;display:flex;align-items:center;gap:10px}
.brand-dot{width:22px;height:22px;background:var(--red);flex:none}
.brand-name{font-family:"Bitter",serif;font-weight:700;font-size:21px;line-height:22px;color:var(--navy);text-transform:uppercase}
.call{left:705px;top:34px;display:flex;align-items:center;gap:12px}
.call small{display:block;font-size:12px;color:var(--navy);font-weight:600}
.call strong{display:block;font-size:17px;color:var(--navy);font-weight:600;letter-spacing:.3px}
.nav{left:344px;top:108px;font-family:"Bitter",serif;font-size:15px;color:var(--navy)}
.nav a{color:inherit;text-decoration:none;position:absolute;white-space:nowrap}
.nav .active{color:var(--red)}
.hero-title{left:0;top:440px;width:1200px;text-align:center;font-family:"Bitter",serif;font-weight:600;font-size:45px;color:var(--white);text-shadow:0 2px 8px rgba(0,0,0,.4)}

/* headings */
.h-sec{font-family:"Bitter",serif;font-weight:700;font-size:24px;line-height:32px;color:var(--navy);text-transform:uppercase}
.rule{width:41px;height:2px;background:var(--red)}
.copy{font-size:14px;line-height:20px;color:var(--text)}

/* welcome */
.mark{left:144px;top:687px;width:296px;height:330px;display:flex;align-items:center;justify-content:center;gap:12px}
.mark-sq{width:34px;height:34px;background:var(--red);flex:none}
.mark-name{font-family:"Bitter",serif;font-weight:700;font-size:34px;line-height:38px;color:var(--navy)}
.welcome-title{left:513px;top:688px;font-family:"Bitter",serif;font-weight:400;font-size:21px;color:var(--navy)}
.welcome-title b{font-weight:700;letter-spacing:.5px;margin-left:8px}
.btn{left:514px;top:930px;width:109px;height:40px;border-radius:20px;background:var(--red);color:var(--white);font-family:"Montserrat",sans-serif;font-weight:700;font-size:11px;display:flex;align-items:center;justify-content:center}

/* why */
.band{left:0;width:1200px;background:var(--grey-band)}
.why-photo{left:643px;top:1065px;width:557px;height:365px;border-radius:12px 0 0 0;
  background:linear-gradient(120deg,#c9dbea 0%,#4a74a2 40%,#1c3a63 75%,#0d1d36 100%)}

/* cards */
.card{width:461px;height:231px;border-radius:19px;background:var(--ink);color:var(--white)}
.card svg{position:absolute;left:44px;top:42px}
.card h3{position:absolute;left:158px;top:40px;font-family:"Bitter",serif;font-weight:700;font-size:16px}
.card p{position:absolute;left:158px;top:80px;width:270px;font-size:12.5px;line-height:17.5px;color:#e8e9ee}

.photo{border-radius:18px}
.chess-photo{left:132px;top:2179px;width:432px;height:375px;background:linear-gradient(135deg,#6f6760 0%,#4a433d 45%,#2d2a27 100%)}
.tablet-photo{left:638px;top:2685px;width:430px;height:451px;background:linear-gradient(150deg,#d8d6d3 0%,#a9b0b8 45%,#5d6670 100%)}

/* footer */
.site-footer{color:var(--white)}
.footer-bg{left:0;top:3199px;width:1200px;height:342px;background:var(--footer)}
.f-brand{left:132px;top:3296px;display:flex;align-items:center;gap:14px}
.f-brand-sq{width:30px;height:30px;background:var(--white);flex:none}
.f-brand-name{font-family:"Bitter",serif;font-weight:700;font-size:32px;line-height:34px;color:var(--white)}
.f-head{font-size:13px;font-weight:700;letter-spacing:.3px;color:var(--white)}
.f-list{font-size:12px;line-height:21px;color:var(--white)}
.f-item{display:flex;gap:10px;align-items:center;font-size:12px;line-height:16px;color:var(--white)}
.f-icon{width:22px;height:22px;border-radius:50%;background:var(--white);flex:none;display:flex;align-items:center;justify-content:center}
.f-line{left:130px;top:3460px;width:933px;height:1px;background:var(--footer-line)}
.f-copy{left:0;top:3500px;width:1200px;text-align:center;font-size:12px;color:var(--white)}
</style>
</head>
<body>

<header>
  <div class="abs hero" role="img" aria-label="Businessman climbing a staircase toward a city skyline"></div>
  <div class="abs hero-light"></div>
  <svg class="abs hero-shape" width="1200" height="680" viewBox="0 0 1200 680">
    <polygon points="0,662 1052,552 1200,662 1200,680 0,680" fill="#ffffff"/>
    <polyline points="0,658 1052,546 1200,656" fill="none" stroke="#d3161c" stroke-width="8"/>
  </svg>
  <div class="abs brand"><span class="brand-dot"></span><span class="brand-name">Crestline<br>Advisory</span></div>
  <div class="abs call">
    <svg width="28" height="28" viewBox="0 0 24 24" fill="none" stroke="#1d2440" stroke-width="1.6" stroke-linejoin="round"><path d="M5 3h4l2 5-2.5 1.5a11 11 0 0 0 6 6L16 13l5 2v4a2 2 0 0 1-2 2A17 17 0 0 1 3 5a2 2 0 0 1 2-2z"/></svg>
    <div><small>Call Us</small><strong>555.014.2290</strong></div>
  </div>
  <nav class="abs nav">
    <a class="active" style="left:0">Home</a>
    <a style="left:78px">About Company</a>
    <a style="left:225px">The Team</a>
    <a style="left:328px">What we do</a>
    <a style="left:439px">Contact us</a>
  </nav>
  <h1 class="abs hero-title">Principal Consultant, MBA</h1>
</header>

<section>
  <div class="abs mark"><span class="mark-sq"></span><span class="mark-name">Crestline<br>Advisory</span></div>
  <h2 class="abs welcome-title">Welcome to <b>CRESTLINE ADVISORY</b></h2>
  <div class="abs rule" style="left:513px;top:722px"></div>
  <p class="abs copy" style="left:513px;top:754px;width:530px">We are a specialist operational excellence firm, delivering consulting and advisory services in six core capabilities, across all industries and all business lines to improve performance, efficiency, profitability, automation and scalability, for clients across Australia. We’re known for our pragmatism, in depth analysis, strategic insight and nurturing long-term client self-sufficiency. We approach business consulting differently, with a Genuine Client Partnership model that builds client capability and rightsized solutions for the client.</p>
  <div class="abs btn">READ MORE</div>
</section>

<section>
  <div class="abs band" style="top:1065px;height:365px"></div>
  <h2 class="abs h-sec" style="left:131px;top:1112px">Why we exist</h2>
  <div class="abs rule" style="left:131px;top:1157px"></div>
  <div class="abs copy" style="left:132px;top:1187px;width:485px">
    <p>Our aim at Tollmer Capital is to be a leading strategy and financial advisory firm across the continent solving complex management problems for small and medium sized enterprises across a wide range of industries.</p>
    <p style="margin-top:20px">We help you scale your business operations to become highly profitable.</p>
    <p style="margin-top:20px">We offer your organization cutting-edge expertise leveraging on first-class, strategic and financial insights that help you simplify and structure your processes to become a lean efficient enterprise.</p>
  </div>
  <div class="abs why-photo" role="img" aria-label="Businessman touching a glowing upward arrow above a bar chart"></div>
</section>

<section>
  <h2 class="abs h-sec" style="left:0;top:1485px;width:1200px;text-align:center">What we do</h2>
  <div class="abs rule" style="left:580px;top:1534px"></div>

  <div class="abs card" style="left:133px;top:1584px">
    <svg width="72" height="64" viewBox="0 0 72 64" fill="none" stroke="#fff" stroke-width="3"><rect x="3" y="8" width="54" height="36" rx="2"/><path d="M22 56h18M31 44v12"/><path d="M10 34l10-8 8 6 8-10"/><circle cx="50" cy="18" r="14" fill="#0e1322"/><path d="M60 28l9 9"/><path d="M45 23l10-10M48 13h7v7"/></svg>
    <h3>Market Entry</h3>
    <p>Lorem ipsum dolor sit amet, consectetur adipiscing elit, sed do eiusmod tempor incididunt ut labore et dolore magna aliqua Ut enim ad minim veniam, quis nostrud exercitation ullamco laboris nisi ut aliquip ex ea commodo</p>
  </div>
  <div class="abs card" style="left:608px;top:1584px">
    <svg width="76" height="64" viewBox="0 0 76 64" fill="#fff"><rect x="4" y="46" width="12" height="16"/><rect x="22" y="38" width="12" height="24"/><rect x="40" y="42" width="12" height="20"/><rect x="58" y="26" width="12" height="36"/><path d="M4 36l18-14 14 8 26-22" fill="none" stroke="#fff" stroke-width="4"/><path d="M56 4h14v14z"/></svg>
    <h3>Strategy Analytics</h3>
    <p>Sed ut perspiciatis unde omnis iste error sit voluptatem accusantium doloremque laudantium, totam rem aperiam, eaque ipsa quae ab illo inventore veritatis et quasi architecto</p>
  </div>
  <div class="abs card" style="left:133px;top:1837px">
    <svg width="56" height="66" viewBox="0 0 56 66" fill="none" stroke="#fff" stroke-width="3"><rect x="4" y="4" width="48" height="58" rx="5"/><rect x="11" y="11" width="34" height="12"/><g fill="#fff" stroke="none"><rect x="11" y="30" width="8" height="6"/><rect x="24" y="30" width="8" height="6"/><rect x="37" y="30" width="8" height="6"/><rect x="11" y="40" width="8" height="6"/><rect x="24" y="40" width="8" height="6"/><rect x="37" y="40" width="8" height="6"/><rect x="11" y="50" width="8" height="6"/><rect x="24" y="50" width="8" height="6"/><rect x="37" y="50" width="8" height="6"/></g></svg>
    <h3>Finance + Accounting + Insurance</h3>
    <p>But I must explain to you how all this mistaken idea of denouncing pleasure and praising pain was born and I will give you a complete account of the system, and expound the actual teachings of the great explorer of the truth, the master-builder.</p>
  </div>
  <div class="abs card" style="left:608px;top:1837px">
    <svg width="56" height="70" viewBox="0 0 56 70" fill="#fff"><path d="M28 2c10 8 14 20 13 38H15C14 22 18 10 28 2z"/><circle cx="28" cy="22" r="5" fill="#0e1322"/><path d="M15 30l-9 10v8l9-4zM41 30l9 10v8l-9-4z"/><rect x="20" y="50" width="4" height="8"/><rect x="26" y="52" width="4" height="14"/><rect x="32" y="50" width="4" height="8"/></svg>
    <h3>Advise for Early Stage Startups</h3>
    <p>Nam libero tempore, cum soluta nobis est eligendi optio cumque nihil impedit quo minus id quod maxime placeat facere possimus, omnis voluptas assumenda est, omnis&nbsp; dolor repellendus.</p>
  </div>
</section>

<section>
  <div class="abs band" style="top:2127px;height:485px"></div>
  <div class="abs photo chess-photo" role="img" aria-label="Hand moving a chess piece on a board"></div>
  <h2 class="abs h-sec" style="left:598px;top:2175px;width:460px">Process improvement within government</h2>
  <div class="abs rule" style="left:600px;top:2253px"></div>
  <p class="abs copy" style="left:601px;top:2284px;width:470px">Across the three levels of Government – Federal, State/Territory and Local – leaders continually face complex decisions around how to allocate limited resources to best service their citizens.&nbsp; In the past, Governments have faced criticism for an over reliance on bureaucracy and an inability to adapt or even prepare for the future.&nbsp; However, the trend among global leaders now is one of innovation both in how they run the business of Government and in the services they apply their resources to.&nbsp; Programs of innovation and transformation are actively sponsored to promote a more competitive and viable society.&nbsp; A focus on reducing waste is leading to more efficient, cost effective government bodies underpinned by the adoption of technology and process improvement techniques.&nbsp; And of course the safety and security (physical and data) of its citizens remains a primary goal in a world facing an unparalleled level of technological advance.</p>
</section>

<section>
  <h2 class="abs h-sec" style="left:132px;top:2675px;width:460px">Technology analysis within healthcare</h2>
  <div class="abs rule" style="left:132px;top:2754px"></div>
  <div class="abs copy" style="left:135px;top:2786px;width:459px;text-align:justify">
    <p>Australia’s healthcare system is a complex web of public and private providers, settings, participants and supporting mechanisms. Health providers include medical practitioners, nurses, allied and other health professionals, hospitals, clinics and government agencies and private providers. These providers deliver a complete range of services across many levels, from public health and preventive services in the community, to primary health care, emergency health services, hospital-based treatment, and rehabilitation and palliative care.</p>
    <p style="margin-top:26px">We work closely with both the Public sector health services through the 3 levels of government and the Private sector health service providers to drive efficiency across their diverse range of services.&nbsp; Through best practise business process re-engineering, the pragmatic use of toolsets such as Lean Six Sigma and a deep understanding of Business &amp; Technology Change, we drive significant cost and efficiency gains across all types of healthcare from hospital to aged care facilities and everything in between.</p>
  </div>
  <div class="abs photo tablet-photo" role="img" aria-label="Hands holding a tablet showing business charts beside a coffee cup"></div>
</section>

<footer class="site-footer">
  <div class="abs footer-bg"></div>
  <div class="abs f-brand"><span class="f-brand-sq"></span><span class="f-brand-name">CRESTLINE<br>ADVISORY</span></div>

  <div class="abs f-head" style="left:496px;top:3242px">MENU</div>
  <div class="abs f-list" style="left:496px;top:3277px">HOME<br>ABOUT COMPANY<br>THE TEAM<br>WHAT WE<br>CONTACT US</div>

  <div class="abs f-head" style="left:702px;top:3242px">CONTACT US</div>
  <div class="abs f-item" style="left:700px;top:3280px"><span class="f-icon"><svg width="10" height="12" viewBox="0 0 10 12"><path d="M5 0a4 4 0 0 1 4 4c0 3-4 8-4 8S1 7 1 4a4 4 0 0 1 4-4z" fill="#111729"/><circle cx="5" cy="4" r="1.5" fill="#fff"/></svg></span><span>2150 Harbor Lane<br>Ashfield, CA 90410</span></div>
  <div class="abs f-item" style="left:700px;top:3332px"><span class="f-icon"><svg width="11" height="11" viewBox="0 0 24 24"><path d="M5 3h4l2 5-2.5 1.5a11 11 0 0 0 6 6L16 13l5 2v4a2 2 0 0 1-2 2A17 17 0 0 1 3 5a2 2 0 0 1 2-2z" fill="#111729"/></svg></span><span>Call Us<br>555.014.2290</span></div>
  <div class="abs f-item" style="left:700px;top:3382px"><span class="f-icon"><svg width="11" height="8" viewBox="0 0 11 8"><rect width="11" height="8" fill="#111729"/><path d="M0 0l5.5 4L11 0" fill="none" stroke="#fff"/></svg></span><span>E mail Us<br>info@crestlineadvisory.example</span></div>

  <div class="abs f-head" style="left:958px;top:3242px">FOLLOW US</div>
  <div class="abs f-item" style="left:956px;top:3280px"><span class="f-icon"></span><span>Like us on<br>SOCIALHUB</span></div>
  <div class="abs f-item" style="left:956px;top:3330px"><span class="f-icon"></span><span>Follow us on<br>CHIRPLINE</span></div>
  <div class="abs f-item" style="left:956px;top:3380px"><span class="f-icon"></span><span>Follow us on<br>WORKNET</span></div>

  <div class="abs f-line"></div>
  <div class="abs f-copy">Copyright © 2020 All Rights Reserved</div>
</footer>

</body>
</html>
```